New, modern business card for growing audiology practice

We need a new business card for our audiology practice. Our logo and website have recently changed (more modern) and we want our business cards to reflect this change.
We conduct hearing tests, perform earwax removals, and fit & dispense hearing aids to our patients. We are a family owned practice in which the owner is the one who works directly with the patient. I have attached logos in various formats to use, as well as two ideas I found on this website; as well as a scanned copy of our current logo. Good luck!

Industry/Entity Type

Business

Contact Information for Business Card

Company name: Tolvera Hearing Center
Provider name: Peter Wolstenby, Au.D. F/NSB
Phone number: (440) 683-5127
Address: 837 W. Lindell Ave. Marlow Falls, OH 44690
email: tolverahearing@postvane.com
website: tolverahearing.com

Colors
000000
aaaaaa
dbdbdb
cacaca
9bcb3c
afd23c
cadf82
b1b1b1

Requirements
Must have
• My card must include information in the "details" section. In the attached images, I found a few that I liked and I would like to model after - "brisky bouncin'" and "Sound Method Center".
• Must be horizontal.
• Must include logos provided. I uploaded them in various file formats and various ways.
• Must match logo font, if possible, if not, please get as close as you can.
Nice to have
• I really like the idea of having a color on one side with just the logo and company name and the contact information and provider name on the other side. I also really like the idea of having the main color dominating on the logo/company side with accent of that same color on the contact side of the card.
Should not have
• Must not be vertical.

```html
<!DOCTYPE html>
<html lang="en">
<head>
<meta charset="utf-8">
<title>Tolvera Hearing Center — Business Card</title>
<link href="https://fonts.googleapis.com/css2?family=Jost:wght@400&family=Roboto:wght@400&family=Saira+Semi+Condensed:wght@600&display=swap" rel="stylesheet">
<style>
  :root {
    --backdrop: #3b3b3b;
    --card: #1d1d1d;
    --green: #6db33f;
    --white: #f1f1f1;
    --muted: #dbdbdb;
  }
  * { margin: 0; padding: 0; box-sizing: border-box; }
  html, body { width: 799px; height: 1200px; overflow: hidden; }
  body {
    background: var(--backdrop);
    display: flex;
    flex-direction: column;
    align-items: center;
    justify-content: center;
    gap: 110px;
  }
  .card {
    position: relative;
    width: 640px;
    height: 366px;
    background: var(--card);
    border-radius: 6px;
    box-shadow: 0 14px 30px rgba(0,0,0,.45);
    color: var(--white);
    overflow: hidden;
  }
  .wordmark {
    font-family: "Jost", sans-serif;
    font-weight: 400;
    text-transform: uppercase;
    color: var(--white);
    display: flex;
    align-items: center;
    gap: 14px;
    white-space: nowrap;
  }
  .wordmark-dot {
    width: 22px; height: 22px;
    border-radius: 50%;
    background: var(--green);
    flex: none;
  }
  /* Front */
  .card-front .wordmark {
    position: absolute;
    left: 70px; top: 130px;
    font-size: 40px;
    letter-spacing: -0.5px;
  }
  .card-front .website {
    position: absolute;
    left: 100px; top: 240px;
    font-family: "Roboto", sans-serif;
    font-size: 17px;
    letter-spacing: 6px;
    color: var(--white);
  }
  .website .accent { color: var(--green); }
  /* Back */
  .brand-mark {
    position: absolute;
    left: 80px; top: 60px;
    width: 140px; height: 140px;
    border-radius: 50%;
    background: var(--green);
  }
  .divider {
    position: absolute;
    left: 290px; top: 50px;
    width: 2px; height: 200px;
    background: var(--green);
  }
  .card-back .wordmark {
    position: absolute;
    left: 40px; top: 280px;
    font-size: 34px;
    letter-spacing: -0.5px;
  }
  .provider {
    position: absolute;
    left: 326px; top: 66px;
    white-space: nowrap;
  }
  .provider-name {
    font-family: "Saira Semi Condensed", sans-serif;
    font-weight: 600;
    font-size: 21px;
    line-height: 26px;
    color: var(--green);
  }
  .provider-role {
    font-family: "Roboto", sans-serif;
    font-size: 14px;
    color: var(--muted);
    margin-top: 2px;
  }
  .contact-list {
    position: absolute;
    left: 326px; top: 136px;
    list-style: none;
    font-family: "Roboto", sans-serif;
    font-size: 16px;
    line-height: 21px;
    color: var(--white);
    white-space: nowrap;
  }
  .contact-list li { display: flex; align-items: flex-start; gap: 10px; }
  .contact-list svg { width: 14px; height: 14px; margin-top: 3px; flex: none; fill: var(--green); }
</style>
</head>
<body>
  <section class="card card-front">
    <div class="wordmark"><span class="wordmark-dot"></span>Tolvera Hearing Center</div>
    <p class="website">www.<span class="accent">tolverahearing</span>.com</p>
  </section>

  <section class="card card-back">
    <div class="brand-mark"></div>
    <div class="divider"></div>
    <div class="provider">
      <p class="provider-name">Peter Wolstenby, Au.D. F/NSB</p>
      <p class="provider-role">Owner - Audiologist</p>
    </div>
    <ul class="contact-list">
      <li>
        <svg viewBox="0 0 14 14" aria-hidden="true"><path d="M7 0a5 5 0 0 0-5 5c0 3.5 5 9 5 9s5-5.5 5-9a5 5 0 0 0-5-5zm0 7a2 2 0 1 1 0-4 2 2 0 0 1 0 4z"/></svg>
        <span>837 W. Lindell Ave.<br>Marlow Falls, OH 44690</span>
      </li>
      <li>
        <svg viewBox="0 0 14 14" aria-hidden="true"><path d="M3 1l2.5 3-1.5 1.5a8 8 0 0 0 4.5 4.5L10 8.5l3 2.5-1.5 2.5C6 13 1 8 .5 2.5z"/></svg>
        <span>(440) 683-5127</span>
      </li>
      <li>
        <svg viewBox="0 0 14 14" aria-hidden="true"><path d="M0 3h14v8H0zM0 3l7 5 7-5v1L7 9 0 4z"/></svg>
        <span>tolverahearing@postvane.com</span>
      </li>
      <li>
        <svg viewBox="0 0 14 14" aria-hidden="true"><circle cx="7" cy="7" r="6.5"/><path d="M.5 7h13M7 .5c-3 3-3 10 0 13M7 .5c3 3 3 10 0 13" stroke="#1d1d1d" stroke-width="1" fill="none"/></svg>
        <span>www.tolverahearing.com</span>
      </li>
    </ul>
    <div class="wordmark"><span class="wordmark-dot"></span>Tolvera Hearing Center</div>
  </section>
</body>
</html>
```